Brightline Energy Product Distribution Brochure

We are looking to have our current brochure for our customers completely redesigned...the idea is to present the relevant information in an attractive way . Our website is brightlineenergyco.example where you can find more information about us. We have included a file with a rough idea of the page order and what each should include but feel free to adapt based on design. The example provided is only for context and doesnt have to be maintained. We will be using the brochure both digitally and in print form. As long as it reads easily and is eye catching, the design can be horizontal or vertical.Final deliverable should be indesign file.

"Our Brands" page: should be limited to one page (space being enough) where it has the header for each one (for example diesel generators) space for one or two lines of text and then the corresponding logos for each of the five categories
Updates

For those asking: the "our brands" page should be a single page layout where there is a header with the corresponding section and space for maybe one line of text followed by the two logos for that category. Each of the product pages should be similar in fashion to the one in the document attached: a photo of the product with some white space and space for the text to be included. We will be posting additional examples today

Target Market(s)

We want to present it to customers both digitally and in print so they can see our products

Industry/Entity Type

Power Generation

Font styles to use
Serif

Requirements
Must have
• Eye catching and able to present the information in a presentable fashion. Rest is up to you.
Nice to have
• Should incorporate the colors of our logo but can also add other depending on design

```html
<!DOCTYPE html>
<html lang="en">
<head>
<meta charset="utf-8">
<title>Brightline Energy Brochure – Inside Pages</title>
<link rel="stylesheet" href="https://fonts.googleapis.com/css2?family=Montserrat:wght@300;400;500;700&display=swap">
<style>
  :root {
    --yellow: #fbc905;
    --yellow-deep: #eab800;
    --ink: #1e1e1e;
    --ink-soft: #2b2b2b;
    --page: #ffffff;
    --backdrop: #ffffff;
    --product-dark: #26282a;
    --product-grey: #a9acae;
  }
  * { box-sizing: border-box; margin: 0; padding: 0; }
  html, body { width: 1200px; height: 1200px; overflow: hidden; background: var(--backdrop); }
  body { position: relative; font-family: "Montserrat", sans-serif; color: var(--ink); }

  .page {
    position: absolute;
    top: 207px;
    width: 556px;
    height: 788px;
    background: var(--page);
    overflow: hidden;
  }
  .page--left { left: 30px; }
  .page--right { left: 606px; }

  .page__art { position: absolute; inset: 0; width: 100%; height: 100%; }

  .page__tab {
    position: absolute; left: 0; top: 36px;
    width: 47px; height: 10px; background: var(--yellow);
  }
  .page__section {
    position: absolute; left: 57px; top: 35px;
    font-size: 10px; font-weight: 400; letter-spacing: 0.02em;
  }
  .brand {
    position: absolute; right: 50px; top: 38px;
    display: flex; align-items: center; gap: 5px;
    font-size: 8.5px; font-weight: 500; letter-spacing: 0.04em;
    color: var(--ink-soft);
  }
  .brand__square { width: 13px; height: 13px; background: var(--yellow); }

  .page__title {
    position: absolute; left: 48px; top: 96px;
    font-size: 32px; font-weight: 400; letter-spacing: -0.01em;
    color: var(--ink);
  }
  .page__subtitle {
    position: absolute; left: 48px; top: 160px;
    font-size: 15.5px; font-weight: 700; color: var(--yellow);
  }
  .page__body {
    position: absolute; left: 48px; top: 184px; width: 191px;
    font-size: 8.6px; line-height: 11.2px; text-align: justify;
    hyphens: auto; color: var(--ink-soft);
  }
  .page__footer {
    position: absolute; left: 48px; top: 752px;
    display: flex; gap: 40px;
    font-size: 7px; font-weight: 700; color: var(--ink);
  }

  .product { position: absolute; }
  .product--controller {
    left: 293px; top: 450px; width: 220px; height: 164px;
    border-radius: 8px;
    background: linear-gradient(180deg, #34373a 0%, var(--product-dark) 100%);
  }
  .product--switch {
    left: 310px; top: 390px; width: 190px; height: 278px;
    background: linear-gradient(90deg, #8f9294 0%, var(--product-grey) 40%, #b9bcbe 100%);
  }
</style>
</head>
<body>

  <section class="page page--left">
    <svg class="page__art" viewBox="0 0 695 985" preserveAspectRatio="none" aria-hidden="true">
      <defs>
        <linearGradient id="yellowShadeA" x1="0" y1="0" x2="1" y2="1">
          <stop offset="0" stop-color="var(--yellow)"/>
          <stop offset="0.55" stop-color="var(--yellow)"/>
          <stop offset="1" stop-color="var(--yellow-deep)"/>
        </linearGradient>
      </defs>
      <polyline points="695,88 520,262 695,437" fill="none" stroke="var(--yellow)" stroke-width="1.3"/>
      <polyline points="0,398 140,540 0,680" fill="none" stroke="var(--yellow)" stroke-width="1.3"/>
      <polygon points="512,322 695,505 695,860 570,985 0,985 0,680 107,680" fill="url(#yellowShadeA)"/>
      <polygon points="512,372 695,555 695,748 495,948 215,675" fill="var(--page)"/>
    </svg>

    <div class="page__tab"></div>
    <div class="page__section">OUR STOCK</div>
    <div class="brand"><span class="brand__square"></span>BRIGHTLINE ENERGY</div>

    <h1 class="page__title">CONTROLLERS</h1>
    <h2 class="page__subtitle">CONTROLLERS</h2>
    <p class="page__body">Fugiant pelluptatis rempe nectibea nati nobitate voluptatur, verum dolorerrum velectur, ut fugit aut aborporepe volluptatem in pro beatios molendi genihillis non nonsequ aersped estius seque volupis es sanis ad que volupta quamus ipic te videndene solum esercid que re audam, nonem es atempos re nim cus et volorument fuga. Da am fugia ipidel maios everum ut venient officit quidi ut quo</p>

    <div class="product product--controller" role="img" aria-label="Photo of a black generator control module with a green display screen and control buttons"></div>

    <div class="page__footer"><span>11</span><span>WWW.BRIGHTLINEENERGYCO.EXAMPLE</span></div>
  </section>

  <section class="page page--right">
    <svg class="page__art" viewBox="0 0 695 985" preserveAspectRatio="none" aria-hidden="true">
      <defs>
        <linearGradient id="yellowShadeB" x1="0" y1="0" x2="1" y2="1">
          <stop offset="0" stop-color="var(--yellow)"/>
          <stop offset="0.55" stop-color="var(--yellow)"/>
          <stop offset="1" stop-color="var(--yellow-deep)"/>
        </linearGradient>
      </defs>
      <polyline points="695,88 520,262 695,437" fill="none" stroke="var(--yellow)" stroke-width="1.3"/>
      <polyline points="0,398 140,540 0,680" fill="none" stroke="var(--yellow)" stroke-width="1.3"/>
      <polygon points="512,322 695,505 695,860 570,985 0,985 0,680 107,680" fill="url(#yellowShadeB)"/>
      <polygon points="512,372 695,555 695,748 495,948 215,675" fill="var(--page)"/>
    </svg>

    <div class="page__tab"></div>
    <div class="brand"><span class="brand__square"></span>BRIGHTLINE ENERGY</div>

    <h1 class="page__title">TRANSFER SWITCHES</h1>
    <h2 class="page__subtitle">CONTROLLERS</h2>
    <p class="page__body" style="width:207px">Fugiant pelluptatis rempe nectibea nati nobitate voluptatur, verum dolorerrum velectur, ut fugit aut aborporepe volluptatem in pro beatios molendi genihillis non nonsequ aersped estius seque volupis es sanis ad que volupta quamus ipic te videndene solum esercid que re audam, nonem es atempos re nim cus et volorument fuga. Da am fugia ipidel maios everum ut venient officit quidi ut quo</p>

    <div class="product product--switch" role="img" aria-label="Photo of a grey automatic transfer switch cabinet with a control display on its door"></div>

    <div class="page__footer"><span>12</span><span>WWW.BRIGHTLINEENERGYCO.EXAMPLE</span></div>
  </section>

</body>
</html>
```